Professional Website for Leading Global Private Equity Real Estate Company

The company is a leading global Private Equity Real Estate (PERE). We need a homepage design, an inner page design, and color/font tweaks to the logo (color should be more soothing than current blue used in the logo). The logo website should project the company as global, professional, experienced, trustworthy, accessible, YOUNG, DYNAMIC, hi-tech. PLEASE SEE the attached Design Brief Word Doc for details.

Target Market(s)

institional investors and wealthy private individuals

Industry/Entity Type

Finance

Number of Pages Required

2 page

Font styles to use
Sans Serif
Other font styles liked:
• either like in https://www.ferndalequay.com/ or like in presentations (Montserrat Black & Montserrat Light, Century Gothic, Blair ITC, Almoni Neue DL 4.0 AAA Medium, Almoni DL AAA)

Requirements
Must have
• new color palette that is NOT based on current logo. they want a more soothing color palette than the blue in that logo. the new color palette should project: global, professional, experienced, trustworthy, accessible, YOUNG, DYNAMIC, hi-tech.
Nice to have
• the likes these sites: https://www.ferndalequay.com/ and https://www.tvr.law/

```html
<!DOCTYPE html>
<html lang="en">
<head>
<meta charset="utf-8">
<title>About Veltora Real Estate</title>
<link rel="stylesheet" href="https://fonts.googleapis.com/css2?family=Heebo:wght@300;400;500&family=Michroma&display=swap">
<style>
:root{
  --navy:#0f1f3d;
  --accent:#41608f;
  --accent-dark:#34507c;
  --ink:#1e2a3e;
  --body:#4a4f58;
  --mist:#e6e6e7;
  --frost:#eef0f3;
  --white:#ffffff;
  --footer-text:#c9d1de;
}
*{box-sizing:border-box;margin:0;padding:0}
html,body{width:1200px;height:2841px;overflow:hidden;background:var(--white)}
body{position:relative;font-family:"Heebo",sans-serif;color:var(--body)}
.display{font-family:"Michroma",sans-serif;font-weight:400;letter-spacing:.04em}
.abs{position:absolute}

/* header / hero */
.hero{left:0;top:0;width:1200px;height:462px;background:linear-gradient(180deg,#5d6a7c 0%,#2f4661 28%,#3d4a57 60%,#6b5347 85%,#5a4a48 100%)}
.hero-shade{left:0;top:0;width:1200px;height:100px;background:linear-gradient(180deg,rgba(20,25,35,.45),rgba(20,25,35,0))}
.brand{left:102px;top:14px;display:flex;align-items:center;gap:10px;color:var(--white)}
.brand-mark{width:44px;height:44px;border-radius:50%;background:var(--white)}
.brand-name{font-family:"Heebo",sans-serif;font-weight:300;font-size:19px;line-height:22px;letter-spacing:.05em}
.nav{left:356px;top:29px;display:flex;gap:0;font-size:14px;font-weight:400;color:var(--white);letter-spacing:.02em}
.nav span{position:absolute;white-space:nowrap}
.login{left:1010px;top:20px;width:99px;height:34px;border:1.5px solid var(--white);border-radius:17px;color:var(--white);font-size:13px;text-align:center;line-height:31px}
.hero-title{left:0;top:190px;width:1200px;text-align:center;color:var(--white);font-size:41px;line-height:44px}

/* about */
.about-photo{left:130px;top:560px;width:406px;height:406px;border-radius:50%;background:linear-gradient(135deg,#cdd9e6 0%,#4a5666 45%,#20262f 70%,#8a6a44 100%)}
.eyebrow{left:619px;top:603px;font-size:13px;color:var(--accent)}
.about-title{left:619px;top:624px;font-size:28px;color:var(--ink)}
.rule{height:3px;background:var(--accent)}
.about-copy{left:619px;top:692px;width:505px;font-size:15.5px;line-height:23px;font-weight:300;color:var(--body)}
.about-copy p+p{margin-top:11px}

/* mission */
.mission{left:0;top:1048px;width:1200px;height:533px;background:var(--mist)}
.mission-ring{left:108px;top:1104px;width:395px;height:395px;border-radius:50%;background:#dcdcde}
.mission-photo{left:557px;top:1052px;width:643px;height:529px;clip-path:polygon(0 0,100% 0,100% 100%,203px 100%);background:linear-gradient(120deg,#e0e0e0 0%,#8d8d8d 40%,#3b3b3b 70%,#a9a9a9 100%)}
.mission-title{left:127px;top:1162px;font-size:24px;color:var(--ink)}
.mission-copy{left:129px;top:1224px;width:430px;font-size:16.5px;line-height:27px;font-weight:300;color:#3a3f48}
.mission-copy p+p{margin-top:12px}
.btn{background:var(--accent);color:var(--white);border-radius:24px;text-align:center;font-family:"Michroma",sans-serif;letter-spacing:.06em}
.mission-btn{left:122px;top:1390px;width:179px;height:46px;line-height:46px;font-size:12px}

/* newsletter */
.updates{left:0;top:1581px;width:1200px;height:382px;background:linear-gradient(180deg,#3b5076 0%,#2f4366 60%,#28395a 100%)}
.updates-title{left:0;top:1670px;width:1200px;text-align:center;color:var(--white);font-size:30px}
.updates-sub{left:0;top:1718px;width:1200px;text-align:center;color:var(--white);font-size:17.5px;font-weight:300}
.updates-form{left:338px;top:1766px;width:526px;height:55px;display:flex;border-radius:28px;overflow:hidden;background:var(--white)}
.updates-form .field{flex:1;padding-left:30px;line-height:55px;font-size:14.5px;color:#666}
.updates-form .submit{width:140px;background:var(--accent);color:var(--white);line-height:55px;text-align:center;font-family:"Michroma",sans-serif;font-size:13px;letter-spacing:.05em}

/* contact form */
.touch{left:0;top:1963px;width:1200px;height:518px;background:linear-gradient(180deg,#e9ecf0,#f2f3f5 50%,#e8ebef)}
.touch-title{left:0;top:2050px;width:1200px;text-align:center;font-size:30px;color:var(--ink)}
.input{background:var(--white);font-size:13.5px;color:#555;padding-left:24px}
.input.line{height:50px;line-height:50px}

/* footer */
.footer{left:0;top:2481px;width:1200px;height:360px;background:var(--navy)}
.footer-head{font-size:13.5px;color:var(--white);top:2543px}
.footer-links{top:2580px;font-size:13.5px;line-height:27px;color:var(--footer-text);font-weight:300}
.contact-row{left:870px;display:flex;align-items:center;gap:15px;color:var(--white);font-size:13.5px}
.contact-row svg{flex:none}
.socials{left:871px;top:2713px;display:flex;gap:7px}
.socials span{width:27px;height:27px;border-radius:50%;background:var(--white)}
.footer-rule{left:0;top:2790px;width:1200px;height:1px;background:#26365a}
.legal{top:2810px;font-size:12.5px;color:var(--footer-text);font-weight:300}
</style>
</head>
<body>

<!-- hero -->
<div class="abs hero" role="img" aria-label="Aerial photo of a city skyline by the lake at dusk"></div>
<div class="abs hero-shade"></div>
<div class="abs brand"><span class="brand-mark"></span><span class="brand-name">VELTORA<br>REAL ESTATE</span></div>
<nav class="abs nav">
  <span style="left:0">ABOUT US &#8964;</span>
  <span style="left:110px">OUR BUSINESSES &#8964;</span>
  <span style="left:271px">INVESTORS LOBBY</span>
  <span style="left:437px">NEWS</span>
  <span style="left:524px">CONTACT US</span>
</nav>
<div class="abs login">LOG IN</div>
<h1 class="abs hero-title display">ABOUT VELTORA<br>REALESTATE</h1>

<!-- about -->
<div class="abs about-photo" role="img" aria-label="Upward view of glass skyscrapers framed in a circle"></div>
<div class="abs eyebrow display">WHO WE ARE</div>
<h2 class="abs about-title display">VELTORA REAL ESTATE</h2>
<div class="abs rule" style="left:619px;top:665px;width:58px"></div>
<div class="abs about-copy">
  <p>Lorem ipsum dolor sit amet, consectetur adipiscing elit, sed do eiusmod tempor incididunt ut labore et dolore magna aliqua. Ut enim ad minim veniam, quis nostrud exercitation ullamco laboris</p>
  <p>Aisi ut aliquip ex ea commodo consequat. Duis aute irure dolor in reprehenderit in voluptate velit esse cillum dolore eu fugiat nulla pariatur. Excepteur sint occaecat cupidatat non proident, sunt in culpa qui officia deserunt mollit anim id est laborum.mmodo consequat. Duis aute irure dolor in reprehenderit in voluptate velit esse cillum dolore eu fugiat nulla pariatur. Excepteur sint occaecat cupidatat non proident, sunt in culpa qui officia deserunt mollit anim id est laborum.</p>
</div>

<!-- mission -->
<div class="abs mission"></div>
<div class="abs mission-ring"></div>
<div class="abs mission-photo" role="img" aria-label="Black and white photo of a team gathered around a laptop at a meeting table"></div>
<h2 class="abs mission-title display">OUR MISSION</h2>
<div class="abs rule" style="left:127px;top:1200px;width:60px"></div>
<div class="abs mission-copy">
  <p>Lorem ipsum dolor sit amet, consectetur adipiscing elit, sed do eiusmod tempor incididunt ut co laboris nisi ut aliquip ex ea commodo consequat.</p>
  <p>Aabor et dolore magna aliqua. Ut enim ad minim veniam, quis nostrud exercitation ullamco labor</p>
</div>
<div class="abs btn mission-btn">LEARN MORE</div>

<!-- newsletter -->
<div class="abs updates" role="img" aria-label="Blue tinted city skyline"></div>
<h2 class="abs updates-title display">STAY UPDATED</h2>
<p class="abs updates-sub">Get our latest insights, firm announcements and Charitable Foundation updates.</p>
<div class="abs updates-form"><span class="field">Email address</span><span class="submit">SUBSCRIBE</span></div>

<!-- contact form -->
<div class="abs touch"></div>
<h2 class="abs touch-title display">GET IN TOUCH</h2>
<div class="abs rule" style="left:569px;top:2091px;width:81px"></div>
<div class="abs input line" style="left:237px;top:2125px;width:368px">First Name</div>
<div class="abs input line" style="left:615px;top:2125px;width:368px">Last Name</div>
<div class="abs input line" style="left:237px;top:2181px;width:368px">Phone Number</div>
<div class="abs input line" style="left:615px;top:2181px;width:368px">Email address</div>
<div class="abs input" style="left:237px;top:2239px;width:746px;height:92px;padding-top:12px;padding-left:22px">Message</div>
<div class="abs btn" style="left:504px;top:2348px;width:215px;height:50px;line-height:50px;font-size:14px">SUBMIT NOW</div>

<!-- footer -->
<footer class="abs footer"></footer>
<div class="abs footer-head display" style="left:135px">IMPORTANT LINKS</div>
<div class="abs footer-head display" style="left:405px">EXPLORE VELTORA REAL ESTATE</div>
<div class="abs footer-head display" style="left:868px">CONTACT DETAILS</div>
<div class="abs footer-links" style="left:136px;top:2576px">About Us<br>Our Businesses<br>Investor Lobby<br>News<br>Contact Us</div>
<div class="abs footer-links" style="left:406px">Private Equity<br>Real Estate<br>Credit<br>Strategic Partners<br>Tactical Opportunities<br>Infrastructure</div>
<div class="abs footer-links" style="left:609px">Insurance Solutions<br>Life Sciences<br>Portfolio Operations<br>Technology and Innovations<br>Registered Products</div>

<div class="abs contact-row" style="top:2583px">
  <svg width="28" height="28" viewBox="0 0 28 28"><circle cx="14" cy="14" r="14" fill="#fff"/><path d="M14 6a5.5 5.5 0 0 0-5.5 5.5C8.5 16 14 22 14 22s5.5-6 5.5-10.5A5.5 5.5 0 0 0 14 6z" fill="#0f1f3d"/><circle cx="14" cy="11.5" r="2" fill="#fff"/></svg>
  <span style="line-height:17px">482 N Harbor Ln Suite B<br>Cedar Bay, FL 30012</span>
</div>
<div class="abs contact-row" style="top:2629px">
  <svg width="28" height="28" viewBox="0 0 28 28"><circle cx="14" cy="14" r="14" fill="#fff"/><path d="M10 7l3 3-1.6 2.2a9 9 0 0 0 4.4 4.4L18 15l3 3-2 2.5C13 20 8 15 7.5 9z" fill="#0f1f3d"/></svg>
  <span style="font-size:15px;font-weight:500">555-014-2280</span>
</div>
<div class="abs contact-row" style="top:2666px">
  <svg width="28" height="28" viewBox="0 0 28 28"><circle cx="14" cy="14" r="14" fill="#fff"/><rect x="7.5" y="9.5" width="13" height="9" fill="none" stroke="#0f1f3d" stroke-width="1.6"/><path d="M7.5 9.5l6.5 5 6.5-5" fill="none" stroke="#0f1f3d" stroke-width="1.6"/></svg>
  <span>hello@veltorarealestate.com</span>
</div>
<div class="abs socials"><span></span><span></span><span></span><span></span></div>

<div class="abs footer-rule"></div>
<div class="abs legal" style="left:133px">Copyright &copy; 2022 Veltora Realestate</div>
<div class="abs legal" style="left:830px">Terms of Use &nbsp;|&nbsp; Sitemap &nbsp;|&nbsp; Privacy Policy</div>

</body>
</html>
```